Wordpress Website design partner needed for an Arabic Language Institute for English Speakers

We are an online Arabic Language institute, targeting English Speakers around the world and we provide online courses and private group and one on one classes
We are looking for a total of 5 pages designed.
The Design should be mobile-first, and then provide PC for any differences.
I am looking for a consistent design with a lot of white space and in line with our Logo colours.
Images used should be around the theme of Arabic Language/Islamic in Nature, so please do not use any illustrations or images of animals or human beings except for silhouettes or images without faces visible, such as someone facing other way or below torso or hands etc.
The website will eventually be prepared for Wordpress using Divi.
I will provide a very structured outline of what elements and modules each page should have. Therefore I am looking for someone that has an eye for detail and is precise in executing requirements.
I decided to post on this site because I am looking for a long-term partner that can take care of any of our design needs as they come up.
More details to follow
I will do abit more research tomorrow to suggest sample sites
Updates
Target Market(s)
English speakers that want to learn Arabic for Religous purposes such as understanding the Quran
Industry/Entity Type
Education
Colors
Designer to choose colors to be used in the design.
Requirements
Must have
- Mobile First, and design for PC for changes
- Consistency
- Plenty of White Space
- Colour Palette based on Logo
- Colour and Transparent/White Header for when scrolling
- Big Call to Action buttons with contrasting colors
- A consistent footer for all pages with
- -Social Media Icons
- -Contact us
- -Sitemap
- -Copyright
- -Logo
- Anything with a hashtag (#) beforehand in the Doc file means it should be a module like the modules used in Divi Theme, Please check the following website for an explanation of what each module consists of and some examples of it in use. https://www.pelmorashowcase.net/pelmora-blocks-guide/
Nice to have
- Parallax Effect
Should not have
- illustrations or images of animals or human beings except for silhouettes or images without faces visible, such as someone facing other way or below torso or hands etc.

```html
<!DOCTYPE html>
<html lang="en">
<head>
<meta charset="utf-8">
<title>Qalam Arabic Academy</title>
<link href="https://fonts.googleapis.com/css2?family=IBM+Plex+Sans:wght@300;400;500;600;700&display=swap" rel="stylesheet">
<style>
:root{
  --blue:#1450a8;
  --blue-deep:#0c3f8e;
  --blue-dark:#0a3274;
  --teal:#2896b0;
  --ink:#1d1d1d;
  --text:#3a3a3a;
  --pale:#f3f1f1;
  --night:#262626;
  --white:#ffffff;
}
*{box-sizing:border-box;margin:0;padding:0}
html,body{width:1200px;height:4016px;overflow:hidden}
body{font-family:"IBM Plex Sans",Arial,sans-serif;color:var(--text);background:var(--white);position:relative}
section,header,footer{position:absolute;left:0;width:1200px;overflow:hidden}
.abs{position:absolute}
.btn{position:absolute;display:flex;align-items:center;justify-content:center;border-radius:30px;font-weight:600;text-transform:uppercase;letter-spacing:.3px}
.section-title{position:absolute;left:0;width:1200px;text-align:center;font-weight:600;font-size:26px;color:var(--ink);letter-spacing:.5px}
.rule{position:absolute;height:3px;width:52px;background:var(--teal)}

/* Hero */
.hero{top:0;height:478px;background:linear-gradient(115deg,#0f3f8f 0%,#1553ae 55%,#1a5cb8 100%)}
.hero-skyline{left:0;top:130px;width:380px;height:348px;background:linear-gradient(180deg,rgba(255,255,255,0) 0%,rgba(8,40,100,.35) 100%)}
.nav{position:absolute;top:62px;left:0;width:1200px;height:40px}
.nav a{position:absolute;top:8px;color:var(--white);font-size:15px;font-weight:500;text-decoration:none;letter-spacing:.3px}
.nav a.current{color:#5fb6d6;text-decoration:underline}
.nav .sep{position:absolute;top:4px;width:1px;height:30px;background:rgba(255,255,255,.7)}
.brand-top{position:absolute;left:550px;top:40px;width:100px;height:84px;display:flex;align-items:center;justify-content:center;color:var(--white);font-weight:600;font-size:22px;letter-spacing:1px}
.login{left:972px;top:62px;width:94px;height:39px;border:2px solid var(--white);color:var(--white);font-size:14px}
.hero h1{position:absolute;left:131px;top:168px;color:var(--white);font-size:28px;font-weight:700;letter-spacing:.5px}
.hero p{position:absolute;left:131px;top:220px;width:360px;color:var(--white);font-size:17.5px;line-height:24px}
.btn-start{left:131px;top:377px;width:220px;height:39px;background:var(--teal);color:var(--white);font-size:15px}
.btn-call{left:355px;top:377px;width:126px;height:39px;border:2px solid var(--teal);color:#4fb0cf;font-size:15px}
.video{left:544px;top:171px;width:525px;height:267px;background:linear-gradient(135deg,#5a4632 0%,#b89a72 45%,#6f5434 75%,#3a2c20 100%)}

/* Benefits */
.benefits{top:478px;height:500px;background:var(--white)}
.benefits-bg{left:0;top:40px;width:1200px;height:460px;background:linear-gradient(180deg,rgba(235,235,238,0) 0%,#eeeef1 70%,#e6e6ea 100%)}
.benefit{position:absolute;top:150px;width:260px;text-align:center}
.benefit svg{display:block;margin:0 auto}
.benefit h3{margin-top:28px;font-size:20px;font-weight:600;color:var(--ink)}
.benefit p{margin-top:14px;font-size:14.5px;line-height:19px;color:var(--text)}

/* Banner */
.banner{top:978px;height:499px;background:linear-gradient(100deg,#3b1a08 0%,#c0540f 28%,#e9962e 55%,#f1d88e 80%,#e9e7b8 100%)}
.banner-lantern{left:60px;top:20px;width:230px;height:479px;background:radial-gradient(ellipse at 50% 60%,#ffb347 0%,#d35f0f 45%,rgba(70,25,5,.6) 80%)}
.banner-brand{left:550px;top:80px;width:300px;color:#3c3c3c;font-size:32px;font-weight:600;letter-spacing:6px;line-height:40px}
.banner-brand span{display:block;font-size:16px;letter-spacing:5px;line-height:26px}
.banner h2{position:absolute;left:550px;top:200px;width:470px;color:var(--white);font-size:28px;line-height:36px;font-weight:700;text-transform:uppercase;text-shadow:0 2px 4px rgba(0,0,0,.35)}
.banner p{position:absolute;left:553px;top:285px;width:460px;color:var(--white);font-size:19px;line-height:24px;font-weight:600;text-shadow:0 1px 3px rgba(0,0,0,.35)}
.btn-get{left:556px;top:396px;width:158px;height:38px;background:var(--teal);color:var(--white);font-size:15px}
.arrow{position:absolute;top:240px}

/* Testimonials */
.testimonials{top:1477px;height:583px;background:var(--white)}
.quote{position:absolute;top:170px;width:456px;height:198px;background:var(--pale);padding:34px 70px 34px 37px;font-size:13.5px;line-height:21px;color:var(--text)}
.author{position:absolute;top:393px;display:flex;align-items:center;gap:14px}
.avatar{width:46px;height:46px;border-radius:50%;background:linear-gradient(160deg,#d8c6a0,#7a5a3a)}
.author b{display:block;font-size:13px;color:var(--ink);font-weight:600}
.author small{display:block;font-size:12px;color:var(--text)}
.stars{color:var(--teal);font-size:12px;letter-spacing:2px}
.dots{position:absolute;top:505px;left:558px;display:flex;gap:7px}
.dots i{width:8px;height:8px;border-radius:50%;background:#c9c9c9}
.dots i.on{background:var(--teal)}

/* Strategies */
.strategies{top:2060px;height:450px;background:var(--pale)}
.hands-photo{left:0;top:0;width:612px;height:450px;background:linear-gradient(135deg,#c9b9c4 0%,#e9d6cd 40%,#b99a86 65%,#8fb8c8 100%)}
.strategies h2{position:absolute;left:679px;top:74px;width:360px;font-size:27px;line-height:36px;font-weight:600;color:var(--ink);text-transform:uppercase}
.strategies p{position:absolute;left:680px;top:211px;width:370px;font-size:15px;line-height:21px}
.btn-book{left:681px;top:333px;width:196px;height:49px;background:var(--teal);color:var(--white);font-size:16px}

/* Countdown */
.countdown{top:2510px;height:131px;background:linear-gradient(90deg,#2a2a2a,#3a3a3a 50%,#2a2a2a);color:var(--white)}
.countdown .label{position:absolute;left:195px;top:46px;font-size:27px;font-weight:300}
.unit{position:absolute;top:24px;width:110px;text-align:center}
.unit b{display:block;font-size:50px;font-weight:300;line-height:56px}
.unit small{display:block;font-size:13px;color:#aaa}
.colon{position:absolute;top:30px;font-size:40px;font-weight:300}

/* Features */
.features{top:2641px;height:611px;background:linear-gradient(160deg,#0f3f92 0%,#1a57b3 50%,#0f4296 100%)}
.features .section-title{color:var(--white)}
.feature-panel{left:131px;top:142px;width:938px;height:403px;background:var(--white)}
.tabs{position:absolute;left:4px;top:0;width:250px;height:403px}
.tab{position:absolute;left:0;width:250px;display:flex;align-items:center;justify-content:center;text-align:center;font-size:15px;color:var(--white);background:var(--blue-deep);font-weight:500;padding:0 55px}
.tab.active{background:var(--white);color:var(--blue);font-weight:600}
.feature-panel h3{position:absolute;left:334px;top:55px;font-size:35px;font-weight:400;color:var(--ink)}
.feature-panel p{position:absolute;left:336px;top:128px;width:520px;font-size:16px;line-height:21px;color:var(--text)}

/* Contact */
.contact{top:3252px;height:352px;background:var(--blue)}
.contact h2{position:absolute;left:131px;top:62px;color:var(--white);font-size:30px;font-weight:600}
.contact p{position:absolute;left:131px;top:108px;width:490px;color:#e6eefa;font-size:15px;line-height:21.5px}
.field{position:absolute;left:695px;width:372px;height:47px;background:var(--white);padding:0 17px;display:flex;align-items:center;font-size:15px;color:#555}
.btn-join{left:695px;top:249px;width:372px;height:54px;border-radius:0;background:var(--teal);color:var(--white);font-size:21px;font-weight:600}

/* Footer */
.site-footer{top:3604px;height:412px;background:var(--night);color:var(--white)}
.site-footer h4{position:absolute;font-size:13px;font-weight:600;letter-spacing:.5px}
.info{position:absolute;display:flex;align-items:center;gap:16px;font-size:14px;line-height:17px}
.info small{display:block;font-size:11px}
.ico{width:34px;height:34px;border-radius:50%;background:var(--teal);display:flex;align-items:center;justify-content:center;flex:none}
.social .ico{width:30px;height:30px}
.frame{position:absolute;left:430px;top:60px;width:341px;height:165px;border-left:1px solid #bbb;border-right:1px solid #bbb;border-bottom:1px solid #bbb}
.footer-brand{position:absolute;left:430px;top:90px;width:341px;text-align:center;font-size:30px;font-weight:600;letter-spacing:4px}
.footer-brand span{display:block;font-size:12px;letter-spacing:4px;margin-top:4px}
.footer-nav{position:absolute;left:0;top:256px;width:1200px;text-align:center;font-size:14px;font-weight:600}
.footer-nav a{color:var(--white);text-decoration:none;margin:0 7px}
.footer-rule{left:131px;top:318px;width:938px;height:1px;background:#555}
.copyright{position:absolute;left:0;top:356px;width:1200px;text-align:center;font-size:11px;color:#ddd}
</style>
</head>
<body>

<header class="hero">
  <div class="abs hero-skyline" role="img" aria-label="Faint silhouette of a domed mosque"></div>
  <nav class="nav">
    <a class="current" style="left:349px">HOME</a>
    <span class="sep" style="left:426px"></span>
    <a style="left:455px">ABOUT US</a>
    <a style="left:662px">COURSES</a>
    <span class="sep" style="left:758px"></span>
    <a style="left:787px">CONTACT US</a>
  </nav>
  <div class="brand-top">QALAM</div>
  <div class="btn login">Login</div>
  <h1>WELCOME TO QALAM</h1>
  <p>The Arabic Language Academy which helps understand Allah's words and the Noble Prophets teachings directly in the most Effective, Efficient and Effortless way. Never rely on translations again!</p>
  <div class="btn btn-start">Start Learning Now</div>
  <div class="btn btn-call">Call Now</div>
  <div class="abs video" role="img" aria-label="Video still of an open Quran resting on a wooden stand"></div>
</header>

<section class="benefits">
  <div class="abs benefits-bg" role="img" aria-label="Pale silhouettes of mosque minarets and domes"></div>
  <h2 class="section-title" style="top:54px">BENEFITS</h2>
  <div class="rule" style="left:574px;top:97px"></div>

  <div class="benefit" style="left:125px">
    <svg width="100" height="100" viewBox="0 0 100 100" fill="none" stroke="#2896b0" stroke-width="5" stroke-linecap="round">
      <path d="M36 62c-6-6-10-12-10-20a24 24 0 0 1 48 0c0 8-4 14-10 20v8H36z"/>
      <path d="M38 78h24M42 86h16"/>
      <path d="M50 4v8M16 18l6 6M84 18l-6 6M4 42h8M88 42h8M14 70l7-5M86 70l-7-5"/>
    </svg>
    <h3>EFFICIENT</h3>
    <p>Lorem ipsum dolor sit amet conse ctetur adipiscing elit sed do eiusmod tempor incididunt ut labore et dolore magna aliqua. Ut enim ad minim veniam quis nos trud .</p>
  </div>

  <div class="benefit" style="left:470px">
    <svg width="110" height="100" viewBox="0 0 110 100" fill="none" stroke="#2896b0" stroke-width="5" stroke-linejoin="round" stroke-linecap="round">
      <path d="M4 34l18-18 16 10 18-6 20 2 14-12 16 18-14 14"/>
      <path d="M22 16l-14 22 34 34c4 4 10 4 12 0"/>
      <path d="M56 20l-16 16c-3 4 2 9 6 6l12-10 30 26c4 4-2 10-6 6"/>
      <path d="M36 62l10 10M44 54l12 12M52 48l14 14"/>
    </svg>
    <h3>EFFECTIVE</h3>
    <p>Lorem ipsum dolor sit amet conse ctetur adipiscing elit sed do eiusmod tempor incididunt ut labore et dolore magna aliqua. Ut enim ad minim veniam quis nos trud .</p>
  </div>

  <div class="benefit" style="left:816px">
    <svg width="100" height="100" viewBox="0 0 100 100" fill="none" stroke="#2896b0" stroke-width="4.5" stroke-linecap="round" stroke-linejoin="round">
      <circle cx="58" cy="30" r="12"/>
      <path d="M58 8v6M58 46v6M36 30h6M74 30h6M42 14l4 4M70 42l4 4M74 14l-4 4M46 42l-4 4"/>
      <path d="M52 30l4 4 8-8"/>
      <rect x="6" y="62" width="14" height="28"/>
      <path d="M20 66h22l14 6h14c4 0 4 7 0 7H54M20 86h34l34-14c5-2 8 4 3 7L58 96H20"/>
    </svg>
    <h3>EFFORTLESS</h3>
    <p>Lorem ipsum dolor sit amet conse ctetur adipiscing elit sed do eiusmod tempor incididunt ut labore et dolore magna aliqua. Ut enim ad minim veniam quis nos trud .</p>
  </div>
</section>

<section class="banner">
  <div class="abs banner-lantern" role="img" aria-label="Glowing ornate lantern over desert dunes at sunset"></div>
  <div class="abs banner-brand">QALAM<span>ARABIC ACADEMY</span></div>
  <h2>Lorem ipsum is simply dummy text of the printing</h2>
  <p>Lorem ipsum dolor sit amet conse ctetur adipiscing elit sed do eiusmod tempor incididunt ut labore et dolore magna aliqua. Ut enim.</p>
  <div class="btn btn-get">Get Started</div>
  <svg class="arrow" style="left:30px" width="30" height="54" viewBox="0 0 30 54" fill="none" stroke="#fff" stroke-width="4" stroke-linecap="round"><path d="M26 4L4 27l22 23"/></svg>
  <svg class="arrow" style="left:1138px" width="30" height="54" viewBox="0 0 30 54" fill="none" stroke="#fff" stroke-width="4" stroke-linecap="round"><path d="M4 4l22 23L4 50"/></svg>
</section>

<section class="testimonials">
  <h2 class="section-title" style="top:56px">TESTIMONIALS</h2>
  <div class="rule" style="left:572px;top:106px"></div>

  <div class="quote" style="left:129px">Lorem ipsum dolor sit amet, consectetur adipiscing elit, sed do eiusmod tempor incididunt ut labore et dolore magna aliqua. Ut enim ad minim veniam, quis nostrud exercitation ullamco laboris nisi ut aliquip ex ea commodo consequat. Duis aute irure dolor in reprehende ullam corporis suscipit laboriosam, nisi ut aliquid ex ea commodi</div>
  <div class="quote" style="left:611px">Lorem ipsum dolor sit amet, consectetur adipiscing elit, sed do eiusmod tempor incididunt ut labore et dolore magna aliqua. Ut enim ad minim veniam, quis nostrud exercitation ullamco laboris nisi ut aliquip ex ea commodo consequat. Duis aute irure dolor in reprehende ullam corporis suscipit laboriosam, nisi ut aliquid ex ea commodi</div>

  <div class="author" style="left:156px">
    <div class="avatar" role="img" aria-label="Reviewer portrait"></div>
    <div><b>SAMIR</b><small>General Manager</small><span class="stars">★★★★★</span></div>
  </div>
  <div class="author" style="left:638px">
    <div class="avatar" role="img" aria-label="Reviewer portrait"></div>
    <div><b>SAMIR</b><small>General Manager</small><span class="stars">★★★★★</span></div>
  </div>

  <div class="dots"><i></i><i></i><i class="on"></i><i></i><i></i></div>
</section>

<section class="strategies">
  <div class="abs hands-photo" role="img" aria-label="Open hands raised in prayer holding prayer beads"></div>
  <h2>7 Learning strategies that will boost your Arabic learning</h2>
  <div class="rule" style="left:680px;top:192px"></div>
  <p>Lorem ipsum dolor sit amet, consectetur adipiscing elit, sed do eiusmod tempor incididunt ut labore et dolore magna aliqua. Ut enim ad minim veniam, quis nostrud exercitation ullamco laboris nisi ut.</p>
  <div class="btn btn-book">Book Your Spot</div>
</section>

<section class="countdown">
  <div class="label">Launching in</div>
  <div class="unit" style="left:394px"><b>156</b><small>Days</small></div>
  <span class="colon" style="left:524px">:</span>
  <div class="unit" style="left:558px"><b>10</b><small>Hours</small></div>
  <span class="colon" style="left:684px">:</span>
  <div class="unit" style="left:722px"><b>31</b><small>Minutes</small></div>
  <span class="colon" style="left:849px">:</span>
  <div class="unit" style="left:888px"><b>55</b><small>Seconds</small></div>
</section>

<section class="features">
  <h2 class="section-title" style="top:51px">FEATURES</h2>
  <div class="abs feature-panel">
    <div class="tabs">
      <div class="tab active" style="top:0;height:70px">24/7 Access</div>
      <div class="tab" style="top:73px;height:86px">Learn at your own Pace</div>
      <div class="tab" style="top:162px;height:75px">Certificate</div>
      <div class="tab" style="top:240px;height:80px">Free Study Material</div>
      <div class="tab" style="top:323px;height:80px">Qualified Teachers</div>
    </div>
    <h3>24/7 Access</h3>
    <p>Lorem ipsum dolor sit amet, consectetur adipiscing elit, sed do eiusmod tempor incididunt ut labore et dolore magna aliqua. Ut enim ad minim veniam, quis nostrud exercitation ullamco laboris nisi ut aliquip ex ea commodo consequat. Duis aute irure dolor in reprehenderit in voluptate velit esse cillum dolore eu fugiat nulla pariatur. Excepteur sint occaecat cupidatat non proident, sunt in culpa qui officia deserunt mollit anim id est laborum. Nemo enim ipsam voluptatem quia voluptas sit aspernatur aut odit aut fugit, sed quia consequuntur magni dolores</p>
  </div>
</section>

<section class="contact">
  <h2>CONTACT US</h2>
  <p>At vero eos et accusamus et iusto odio dignissimos ducimus qui blanditiis praesentium voluptatum deleniti atque corrupti quos dolores et quas molestias excepturi sint occaecati cupiditate non provident, similique sunt in culpa qui officia deserunt mollitia animi, id est laborum et dolorum fuga. Et harum quidem rerum facilis est et expedita distinctio. Nam libero tempore, cum soluta nobis est eligendi optio cumque nihil impedit quo minus id quod maxime placeat facere possimus, omnis voluptas assumenda.</p>
  <div class="field" style="top:62px">First Name</div>
  <div class="field" style="top:121px">Last Name</div>
  <div class="field" style="top:180px">E mail</div>
  <div class="btn btn-join">Join Today</div>
</section>

<footer class="site-footer">
  <h4 style="left:137px;top:60px">CONTACT US</h4>
  <div class="info" style="left:131px;top:112px">
    <span class="ico"><svg width="16" height="16" viewBox="0 0 24 24" fill="#fff"><path d="M6.6 10.8a15 15 0 0 0 6.6 6.6l2.2-2.2c.3-.3.7-.4 1-.2 1.1.4 2.3.6 3.6.6.6 0 1 .4 1 1V20c0 .6-.4 1-1 1A17 17 0 0 1 3 4c0-.6.4-1 1-1h3.5c.6 0 1 .4 1 1 0 1.3.2 2.5.6 3.6.1.3 0 .7-.2 1z"/></svg></span>
    <div><small>CALL US</small>555.014.2290</div>
  </div>
  <div class="info" style="left:131px;top:182px">
    <span class="ico"><svg width="16" height="16" viewBox="0 0 24 24" fill="none" stroke="#fff" stroke-width="2"><path d="M3 5h18v14H3z"/><path d="M3 6l9 7 9-7"/></svg></span>
    <div><small>E MAIL US</small>info@qalamacademy.org</div>
  </div>

  <div class="frame"></div>
  <div class="footer-brand">QALAM<span>ARABIC ACADEMY</span></div>
  <nav class="footer-nav"><a>HOME</a><a>ABOUT US</a><a>OUR COURSES</a><a>CONTACT US</a></nav>

  <h4 style="left:893px;top:60px">FOLLOW US</h4>
  <div class="info social" style="left:892px;top:115px"><span class="ico"></span><div>Like us on<br>FRIENDSPACE</div></div>
  <div class="info social" style="left:892px;top:175px"><span class="ico"></span><div>Follow us on<br>CHIRPER</div></div>
  <div class="info social" style="left:892px;top:236px"><span class="ico"></span><div>Follow us on<br>WORKNET</div></div>

  <div class="abs footer-rule"></div>
  <div class="copyright">Copyright © 2020 All Rights Reserved</div>
</footer>

</body>
</html>
```